Diverse, up-scale salon needs eye-catching, unique business cards.

We are looking for a unique business card design for our stylist but that can also be multi functional and used for appointment reminder and referrals. I will need a design in a format that I can modify names and titles going forward. In the past we have had a dark background with the logo on one side, and stylist and contact information on the other but we are open to all ideas. I have included our mission statement as well as branded colors below. The statement doesn't need to go on the card, it's just a reference for target market. We need space for the stylists name, title, instagram handle and then the salons phone number, website and address. I am also open to adding a spot for a qr code linked to the stylist instagram or the salon booking link.

primary brand colors:
#333333 #233415 #36502a #93874a #000000
Mission statement:
Vessolin Hair Studio, a high-end salon located in the lively Downtown Farmington, Michigan, is committed to providing exceptional services in a welcoming and relaxed environment to meet the needs of our diverse clientele.
Our salon specializes in contemporary custom haircuts, coloring, extensions, and barbering and beard grooming services. Our team of skilled stylists is passionate and inventive in their hair styling techniques. At the heart of our salon are values centered on quality, innovation, creativity, and above all, comfort. These core values are evident in every appointment across our customizable array of services.
Our goal is to establish a benchmark for exceptional hair care for every human.
Website: www.vessolinhairstudio.example
instagram: @vessolinhairstudio
address: 41782 Pelham Crest Rd, Farmington MI
phone: 248-613-4087

Industry/Entity Type

Hair Salon

Contact Information for Business Card

Stylist name, title, phone, instagram, website, address, (optional qr code)

Requirements
Should not have
• Does not need mission statement on the card.

```html
<!DOCTYPE html>
<html lang="en">
<head>
<meta charset="utf-8">
<title>Vessolin Hair Studio – Business Card</title>
<link href="https://fonts.googleapis.com/css2?family=Montserrat:wght@400;500;700&display=swap" rel="stylesheet">
<style>
  :root {
    --page-bg: #d9d4cc;
    --card-frost: #ebe8e3;
    --card-edge: #f6f4f0;
    --panel-black: #0c0c0c;
    --brand-gold: #93874a;
    --text-dark: #333333;
    --text-mid: #4a4a4a;
  }
  * { margin: 0; padding: 0; box-sizing: border-box; }
  html, body {
    width: 1200px; height: 1200px; overflow: hidden;
    background: var(--page-bg);
    font-family: "Montserrat", Arial, sans-serif;
  }
  .business-card {
    position: absolute;
    left: 57px; top: 305px;
    width: 1085px; height: 590px;
    border-radius: 24px;
    overflow: hidden;
    background: var(--card-frost);
    border: 2px solid var(--card-edge);
    box-shadow: 0 18px 40px rgba(0,0,0,0.12);
  }
  .logo-panel { position: absolute; inset: 0; width: 100%; height: 100%; }
  .accent-tab {
    position: absolute; left: 0; top: 80px;
    width: 30px; height: 64px;
    background: var(--brand-gold);
    border-radius: 0 12px 12px 0;
  }
  .stylist-name {
    position: absolute; left: 64px; top: 76px;
    font-weight: 700; font-size: 33px; letter-spacing: 1px;
    color: var(--brand-gold);
  }
  .stylist-title {
    position: absolute; left: 64px; top: 122px;
    font-weight: 500; font-size: 24px;
    color: var(--text-mid);
  }
  .salon-address {
    position: absolute; left: 64px; top: 258px;
    font-weight: 500; font-size: 24px; line-height: 41px;
    color: var(--text-dark); font-style: normal;
  }
  .contact-list {
    position: absolute; left: 64px; top: 396px;
    list-style: none;
  }
  .contact-item {
    display: flex; align-items: center; gap: 14px;
    height: 41px;
    font-weight: 500; font-size: 22px;
    color: var(--text-dark);
  }
  .contact-icon { width: 22px; height: 22px; flex: none; }
  .brand-name {
    position: absolute; left: 575px; top: 225px;
    width: 420px; text-align: center;
    font-weight: 700; font-size: 52px; line-height: 70px;
    letter-spacing: 8px; text-transform: uppercase;
    color: var(--brand-gold);
  }
</style>
</head>
<body>
  <div class="business-card">
    <svg class="logo-panel" viewBox="0 0 1085 590" preserveAspectRatio="none" aria-hidden="true">
      <path d="M571 0 C 430 110 410 440 658 590 L1085 590 L1085 0 Z" fill="var(--panel-black)"/>
    </svg>

    <span class="accent-tab"></span>
    <h1 class="stylist-name">MARISOL KEANE</h1>
    <p class="stylist-title">President</p>

    <address class="salon-address">
      41782 Pelham Crest Rd<br>
      Farmington MI
    </address>

    <ul class="contact-list">
      <li class="contact-item">
        <svg class="contact-icon" viewBox="0 0 24 24" aria-hidden="true">
          <path d="M6.6 10.8a15 15 0 0 0 6.6 6.6l2.2-2.2a1 1 0 0 1 1-.25 11.4 11.4 0 0 0 3.6.57 1 1 0 0 1 1 1V20a1 1 0 0 1-1 1A17 17 0 0 1 3 4a1 1 0 0 1 1-1h3.5a1 1 0 0 1 1 1 11.4 11.4 0 0 0 .57 3.6 1 1 0 0 1-.25 1z" fill="var(--text-mid)"/>
        </svg>
        248-613-4087
      </li>
      <li class="contact-item">
        <svg class="contact-icon" viewBox="0 0 24 24" aria-hidden="true">
          <circle cx="12" cy="12" r="8" fill="none" stroke="var(--text-mid)" stroke-width="2"/>
        </svg>
        @vessolinhairstudio
      </li>
      <li class="contact-item">
        <svg class="contact-icon" viewBox="0 0 24 24" aria-hidden="true">
          <g fill="none" stroke="var(--text-mid)" stroke-width="1.8">
            <circle cx="12" cy="12" r="9"/>
            <ellipse cx="12" cy="12" rx="4" ry="9"/>
            <path d="M3 12h18M5 7.5h14M5 16.5h14"/>
          </g>
        </svg>
        www.vessolinhairstudio.example
      </li>
    </ul>

    <p class="brand-name">Vessolin<br>Hair Studio</p>
  </div>
</body>
</html>
```